The Linen Loft Co

We need a business card design for our wardrobe company.
Please visit our website www.gentlelinenlofts.com to get an idea of who we are.

```html
<!DOCTYPE html>
<html lang="en">
<head>
<meta charset="utf-8">
<title>The Linen Loft Co — Business Card</title>
<link rel="stylesheet" href="https://fonts.googleapis.com/css2?family=Roboto:wght@400;500&display=swap">
<style>
  :root {
    --stage: #2b2b2b;
    --card-light: #ffffff;
    --card-dark: #262626;
    --ink: #1f1f1f;
    --rule: #6e6e6e;
    --paper-text: #f2f2f2;
  }
  * { margin: 0; padding: 0; box-sizing: border-box; }
  html, body { width: 1200px; height: 900px; overflow: hidden; }
  body {
    background: var(--stage);
    font-family: "Roboto", Arial, sans-serif;
    color: var(--ink);
    position: relative;
  }
  .card {
    position: absolute;
    left: 262px;
    width: 676px;
    height: 386px;
    border-radius: 4px;
    overflow: hidden;
    box-shadow: 0 12px 30px rgba(0,0,0,.45);
  }
  .card--front { top: 40px; background: var(--card-light); }
  .card--back { top: 470px; background: var(--card-dark); color: var(--paper-text); }

  .holder { position: absolute; left: 44px; top: 44px; }
  .holder__name { font-size: 34px; font-weight: 400; letter-spacing: 1px; text-transform: uppercase; line-height: 1; }
  .holder__role { font-size: 15px; margin-top: 6px; }

  .divider { position: absolute; left: 44px; top: 128px; width: 560px; height: 2px; background: var(--rule); }

  .contacts { position: absolute; left: 44px; top: 150px; list-style: none; font-size: 17px; line-height: 27px; }
  .contacts li { display: flex; align-items: center; gap: 12px; }
  .contacts svg { width: 13px; height: 13px; flex: none; }

  .brand { position: absolute; right: 44px; top: 50px; }
  .brand__row { display: flex; align-items: center; gap: 12px; }
  .brand__square { width: 22px; height: 22px; background: var(--ink); }
  .brand__name { font-size: 18px; font-weight: 500; text-transform: uppercase; letter-spacing: .5px; }
  .brand__tagline { font-size: 14px; margin-top: 4px; margin-left: 34px; }

  .address { position: absolute; right: 72px; top: 150px; text-align: right; font-size: 17px; line-height: 26px; font-style: normal; }

  .wave { position: absolute; left: 0; bottom: 0; width: 676px; height: 120px; }

  .back-brand { position: absolute; left: 0; right: 0; top: 50%; transform: translateY(-50%); text-align: center; }
  .back-brand .brand__row { justify-content: center; gap: 16px; }
  .back-brand .brand__square { width: 34px; height: 34px; background: var(--paper-text); }
  .back-brand .brand__name { font-size: 30px; }
  .back-brand .brand__tagline { font-size: 22px; margin: 8px 0 0 50px; }
</style>
</head>
<body>
  <section class="card card--front" aria-label="Card front">
    <div class="holder">
      <h1 class="holder__name">Daniel Hartley</h1>
      <p class="holder__role">Director</p>
    </div>
    <div class="divider"></div>
    <ul class="contacts">
      <li>
        <svg viewBox="0 0 16 16" aria-hidden="true"><path d="M4 1l3 3-1.5 2a9 9 0 0 0 4.5 4.5L12 9l3 3-2 2.5C7 14 2 9 1.5 3z" fill="none" stroke="#333" stroke-width="1.4"/></svg>
        0207 555 0148
      </li>
      <li>
        <svg viewBox="0 0 16 16" aria-hidden="true"><rect x="1.5" y="3.5" width="13" height="9" fill="none" stroke="#333" stroke-width="1.4"/><path d="M1.5 3.5L8 9l6.5-5.5" fill="none" stroke="#333" stroke-width="1.4"/></svg>
        info@gentlelinenlofts.com
      </li>
      <li>
        <svg viewBox="0 0 16 16" aria-hidden="true"><circle cx="8" cy="8" r="7" fill="#555"/><path d="M1 8h14M8 1c-3 4-3 10 0 14M8 1c3 4 3 10 0 14" fill="none" stroke="#fff" stroke-width="1"/></svg>
        www.gentlelinenlofts.com
      </li>
    </ul>
    <div class="brand">
      <div class="brand__row">
        <span class="brand__square"></span>
        <span class="brand__name">The Linen Loft Co</span>
      </div>
      <p class="brand__tagline">Folded with Quiet Care</p>
    </div>
    <address class="address">
      Arden House, 42 Mill Lane,<br>London N1 4QT
    </address>
    <svg class="wave" viewBox="0 0 676 120" preserveAspectRatio="none" aria-hidden="true">
      <path d="M0 38 C120 50 250 70 340 78 C380 82 395 96 420 104 C440 112 460 112 470 120 L0 120Z" fill="var(--card-dark)"/>
      <path d="M0 26 C140 40 260 58 340 66" fill="none" stroke="var(--card-dark)" stroke-width="4"/>
    </svg>
  </section>

  <section class="card card--back" aria-label="Card back">
    <div class="back-brand">
      <div class="brand__row">
        <span class="brand__square"></span>
        <span class="brand__name">The Linen Loft Co</span>
      </div>
      <p class="brand__tagline">Folded with Quiet Care</p>
    </div>
  </section>
</body>
</html>
```